House-share and Room Rental Website (With Focus on the Bedroom Landing Page)

Looking for website design for our House-share (executive accommodation) and room rental business.

Our company name is: Lodgivo could also be written as LodGivo or lodgivo. Either is fine .. just looking for a nice clean catchy logo to go with the design.

EXAMPLES
These are examples of other websites in this field that are doing well. this is a kind of baseline.
https://nestpartners-example.com.au/
https://www.bunkora-example.com/
https://www.dwelzy-example.com/
https://www.habiquo-example.net/
https://www.cohabiscout-example.com.au/

Our business model is to rent rooms to people looking for high-quality accommodation. We fill the gap between those looking to rent rooms and those with rooms to rent. However, our model is slightly different from those already on the market as we looking to fill a massive gap in the market delivering upmarket rooms for rent.(Executive Accommodation) also in the back end will be coupled with a self management process in the back end.

We offer executive style accommodation that stands out above the rest. With special extras like fire safety.. and management processes that create happier homes. We are looking for a web design package that can help us grow and scale our business. We need a design that is captivating

Our MAIN focus is having a room landing page that stands out from the rest... The core of our business will rely on the promotion of the rooms in a share house... so the whole design relies on the BEDROOM landing page to drive results.

Target Market(s)

We have 2 markets we are aiming at ... the first market is people offering rooms to rent who want the highest rental return. The second market is people looking to rent safe, high-quality rooms, in houses that are well managed and looked after.

Industry/Entity Type

Share Economy

Logo Text

LodGivo

Number of Pages Required

5+ page

Font styles to use
Sans Serif

Colors
3276b5

Requirements
Must have
• A messaging system whereby we can create direct communication between those offering rooms and those looking for rooms.
• A call to action that says " Schedule an Inspection"
• Landing page for promoting rooms
• A home page for showing stock.
• Profile page for those selling rooms
• Profile page for those looking for rooms.
• A scheduling calendar for booking inspections
Nice to have
• Pages where new residents can lock in a room.. pay bond and rents.. and sign contracts
• Notifications
• SMS capabilities in the backend.
Should not have
• No script or handwriting fonts.

```html
<!DOCTYPE html>
<html lang="en">
<head>
<meta charset="utf-8">
<title>LodGivo – The white room</title>
<link href="https://fonts.googleapis.com/css2?family=Lato:wght@300;400;700;900&display=swap" rel="stylesheet">
<style>
:root{
  --brand:#3276b5;
  --ink:#111;
  --muted:#777;
  --faint:#a8a8a8;
  --line:#d9d9d9;
  --bg:#fff;
}
*{box-sizing:border-box;margin:0;padding:0}
html,body{width:880px;height:1200px;overflow:hidden;background:var(--bg)}
body{position:relative;font-family:'Lato',sans-serif;color:var(--ink)}
.abs{position:absolute}
svg{display:block}
.ico{fill:none;stroke:#333;stroke-width:1.2;stroke-linecap:round;stroke-linejoin:round}

/* header */
.site-header .brand{left:80px;top:22px;display:flex;align-items:center;gap:5px;font-weight:900;font-size:12px;color:var(--ink)}
.brand-mark{width:9px;height:9px;background:var(--brand)}
.main-nav{right:80px;top:16px;display:flex;align-items:center;gap:20px;font-size:6.5px;font-weight:700;letter-spacing:.6px}
.main-nav .sep{width:1px;height:7px;background:var(--ink)}
.signin{border:1px solid var(--brand);color:var(--brand);padding:5px 12px}

/* gallery */
.photo{background:linear-gradient(160deg,#e6e3de,#bdb6ad 60%,#8d8378)}
.photo.soft{background:linear-gradient(160deg,#d9d5cf,#b5ada4 55%,#8a7d6c)}
.photo.vase{background:linear-gradient(180deg,#f0f0f0,#d4d4d2 60%,#4a423e)}

/* listing head */
.eyebrow{font-size:8px;font-weight:700;letter-spacing:.2px}
.room-title{font-size:26px;font-weight:300;line-height:1}
.room-type{font-size:13px;font-weight:900;letter-spacing:.1px}
.rating{display:flex;align-items:center;gap:2px;font-size:7px}
.rating svg{width:8px;height:8px}
.price-label{font-size:6.5px}
.price{font-size:23px;color:var(--brand);font-weight:700;line-height:1}
.book{background:var(--brand);color:#fff;font-size:7px;letter-spacing:.6px;text-align:center;line-height:19px}
.description{font-size:9.6px;line-height:12.7px}
.owner-photo{border:1px solid var(--line);padding:2px;background:#fff}
.owner-photo div{width:100%;height:100%;background:linear-gradient(180deg,#e8e3dd,#c9bcb0)}
.owner-title{font-size:13px;font-weight:900}
.owner-name{font-size:9.6px}

h2{font-size:13px;font-weight:900}

/* features */
.features{display:flex;left:193px;top:560px;width:493px;justify-content:space-between}
.feature{display:flex;flex-direction:column;align-items:center;width:46px;text-align:center}
.feature svg{width:12px;height:12px}
.feature .k{font-size:3.5px;color:var(--faint);margin-top:2px;text-transform:uppercase}
.feature .v{font-size:6px;margin-top:1px;white-space:nowrap}

/* amenities */
.amenities{left:193px;top:634px;width:240px;display:grid;grid-template-columns:repeat(4,auto);justify-content:start;column-gap:18px;row-gap:18px}
.amenity{display:flex;flex-direction:column;align-items:center;font-size:8px;gap:4px}
.amenity svg{width:28px;height:22px}
.public{left:444px;top:633px;width:120px}
.public li{list-style:none;display:flex;align-items:center;gap:7px;font-size:8px;font-weight:700}
.public li svg{width:14px;height:14px}
.public .sub{font-size:6px;font-weight:400;margin-left:23px;margin-top:3px;margin-bottom:12px}
.public .chev{margin-left:auto;width:8px!important;height:8px!important}
.public li+li{margin-top:9px}

/* location */
.address{font-size:9.6px}
.map{background:linear-gradient(135deg,#e9e8e5,#e0dfdc 40%,#d6e2c9 70%,#e5e4e0)}

/* similar */
.card{position:absolute;top:939px;width:157px}
.card .thumb{height:89px}
.card .city{font-size:7.5px;color:var(--brand);margin-top:12px;font-weight:700}
.card .name{font-size:15px;font-weight:300;margin-top:3px;line-height:1}
.card .type{font-size:10.5px;font-weight:900;margin-top:3px}
.card .rating{margin-top:3px}
.t1{background:linear-gradient(160deg,#3f3a2b,#8f7a55 45%,#cdb58a)}
.t2{background:linear-gradient(160deg,#3a1f24,#6b3a3f 45%,#d8d3cf)}
.t3{background:linear-gradient(160deg,#4a4640,#8d8a83 45%,#4c6aa0)}

/* footer */
.site-footer .rule{left:193px;top:1132px;width:493px;height:1px;background:var(--line)}
.footer-brand{left:193px;top:1141px;display:flex;align-items:center;gap:5px;font-size:12px;font-weight:900;color:var(--faint)}
.footer-brand .brand-mark{background:var(--faint)}
.footer-col{list-style:none;font-size:9px;color:var(--faint);line-height:16px;top:1139px}
</style>
</head>
<body>
<svg width="0" height="0" style="position:absolute">
  <symbol id="star" viewBox="0 0 10 10"><path d="M5 .5l1.4 2.9 3.1.4-2.3 2.2.6 3.1L5 7.6 2.2 9.1l.6-3.1L.5 3.8l3.1-.4z" fill="var(--brand)"/></symbol>
  <symbol id="star-off" viewBox="0 0 10 10"><path d="M5 .5l1.4 2.9 3.1.4-2.3 2.2.6 3.1L5 7.6 2.2 9.1l.6-3.1L.5 3.8l3.1-.4z" fill="#ccc"/></symbol>
  <symbol id="star-half" viewBox="0 0 10 10"><path d="M5 .5l1.4 2.9 3.1.4-2.3 2.2.6 3.1L5 7.6 2.2 9.1l.6-3.1L.5 3.8l3.1-.4z" fill="#ccc"/><path d="M5 .5v7.1L2.2 9.1l.6-3.1L.5 3.8l3.1-.4z" fill="var(--brand)"/></symbol>
  <symbol id="chev" viewBox="0 0 10 10"><path d="M2 3.5l3 3 3-3" fill="none" stroke="#333" stroke-width="1.3"/></symbol>
</svg>

<header class="site-header">
  <div class="abs brand"><span class="brand-mark"></span>LodGivo</div>
  <nav class="abs main-nav">
    <span>BROWSE</span><span>DISCOVER</span><span class="sep"></span><span>LIST YOUR FLAT</span><span class="sep"></span><span>LOGIN</span><span class="signin">SIGN IN</span>
  </nav>
</header>

<section class="gallery">
  <div class="abs photo" style="left:72px;top:57px;width:362px;height:277px" role="img" aria-label="White bedroom with double bed, pendant lights and breakfast tray"></div>
  <div class="abs photo soft" style="left:444px;top:57px;width:362px;height:133px" role="img" aria-label="Pillows and flowers on a wooden bed tray"></div>
  <div class="abs photo vase" style="left:444px;top:201px;width:176px;height:133px" role="img" aria-label="Ceramic vase on a bedside table"></div>
  <div class="abs photo soft" style="left:630px;top:201px;width:176px;height:133px" role="img" aria-label="Close-up of grey satin pillows"></div>
</section>

<section class="listing">
  <div class="abs eyebrow" style="left:193px;top:362px">MELBOURNE</div>
  <h1 class="abs room-title" style="left:192px;top:374px">The white room</h1>
  <div class="abs room-type" style="left:193px;top:404px">DOUBLE BEDROOM</div>
  <div class="abs rating" style="left:193px;top:425px">
    <svg><use href="#star"/></svg><svg><use href="#star"/></svg><svg><use href="#star"/></svg><svg><use href="#star"/></svg><svg><use href="#star"/></svg><span>&nbsp;314</span>
  </div>
  <div class="abs price-label" style="left:444px;top:362px">Rental price (per month)</div>
  <div class="abs price" style="left:444px;top:374px">A$600</div>
  <div class="abs book" style="left:570px;top:374px;width:116px;height:19px">BOOK</div>

  <p class="abs description" style="left:193px;top:447px;width:325px">Donec lobortis urna sed urna tincidunt, a vulputate quam tempor. Donec et ultrices velit. Donec ac pretium justo, sit amet interdum nisi. Vestibulum elementum leo et viverra maximus. Donec molestie diam sagittis feugiat egestas. Proin sollicitudin quam arcu, mollis iaculis erat molestie nec. In finibus egestas facilisis. Etiam tempus justo non aliquet tempus. Maecenas feugiat nisi</p>

  <div class="abs owner-photo" style="left:529px;top:449px;width:31px;height:35px"><div role="img" aria-label="Owner portrait"></div></div>
  <div class="abs owner-title" style="left:571px;top:451px">The Owner</div>
  <div class="abs owner-name" style="left:571px;top:473px">Daniel Marsh</div>
</section>

<section>
  <h2 class="abs" style="left:192px;top:534px">Features</h2>
  <div class="abs features">
    <div class="feature"><svg viewBox="0 0 12 12" class="ico"><circle cx="6" cy="4" r="2.3"/><path d="M2 11c0-2.5 1.8-4 4-4s4 1.5 4 4"/></svg><span class="k">Type</span><span class="v">Single</span></div>
    <div class="feature"><svg viewBox="0 0 12 12" class="ico"><rect x="3" y="1.5" width="6" height="9"/><path d="M3 3.5h6"/></svg><span class="k">Size</span><span class="v">40 Sqm</span></div>
    <div class="feature"><svg viewBox="0 0 12 12" class="ico"><path d="M2 2h4v4H2zM2 6h8l-1 3H4zM5 9v2"/></svg><span class="k">Bathroom</span><span class="v">Private</span></div>
    <div class="feature"><svg viewBox="0 0 12 12" class="ico"><rect x="2" y="1.5" width="8" height="9"/><path d="M5 8V4h1.5a1.2 1.2 0 010 2.4H5"/></svg><span class="k">Parking</span><span class="v">Private</span></div>
    <div class="feature"><svg viewBox="0 0 12 12" class="ico"><circle cx="6" cy="6" r="4.5"/><path d="M3 8.5l6-5M3.5 6.5h5"/></svg><span class="k">Smoking</span><span class="v">Not allowed</span></div>
    <div class="feature"><svg viewBox="0 0 12 12" class="ico"><path d="M9 2l1.5 1.5L5 9H3.5V7.5zM2 10.5h8"/></svg><span class="k">Min stay</span><span class="v">3 months</span></div>
    <div class="feature"><svg viewBox="0 0 12 12" class="ico"><path d="M2 10V3h8v7M2 7h8M3.5 7V5h5v2"/></svg><span class="k">Bed size</span><span class="v">200x200</span></div>
    <div class="feature"><svg viewBox="0 0 12 12" class="ico"><circle cx="4" cy="4" r="1.8"/><circle cx="8.5" cy="4" r="1.8"/><path d="M1 10c0-2 1.3-3.2 3-3.2S7 8 7 10M6.5 7.2c.5-.3 1.2-.4 2-.4 1.7 0 2.5 1.2 2.5 3.2"/></svg><span class="k">Flatmates</span><span class="v">Professionals</span></div>
    <div class="feature"><svg viewBox="0 0 12 12" class="ico"><rect x="3.5" y="1" width="5" height="10"/><path d="M7 6h.5"/></svg><span class="k">Entrance</span><span class="v">Private</span></div>
    <div class="feature"><svg viewBox="0 0 12 12" class="ico"><path d="M1.5 5a6.5 6.5 0 019 0M3 6.8a4.3 4.3 0 016 0"/><circle cx="6" cy="8.8" r=".6"/></svg><span class="k">Internet</span><span class="v">600mbps</span></div>
  </div>
</section>

<section>
  <h2 class="abs" style="left:193px;top:612px">Amenities</h2>
  <div class="abs amenities">
    <div class="amenity"><svg viewBox="0 0 28 22" class="ico"><path d="M3 17V8h22v9M3 12h22M6 8V5h16v3M4 17v2M24 17v2"/></svg>Furnished</div>
    <div class="amenity"><svg viewBox="0 0 28 22" class="ico"><rect x="5" y="2" width="18" height="14" rx="3"/><path d="M10 19h8"/><text x="14" y="12" font-size="7" text-anchor="middle" stroke="none" fill="#333" font-family="Lato,sans-serif">TV</text></svg>SmartTV</div>
    <div class="amenity"><svg viewBox="0 0 28 22" class="ico"><rect x="7" y="1" width="14" height="20"/><path d="M7 7h14M7 14h14M10 4h3M15 10h3M10 17h3"/></svg>Storage space</div>
    <div class="amenity"><svg viewBox="0 0 28 22" class="ico"><path d="M4 11h20M6 11v10M22 11v10M14 4h7v7h-7zM8 15h4v6"/></svg>Workstation</div>
    <div class="amenity"><svg viewBox="0 0 28 22" class="ico"><rect x="6" y="1" width="16" height="20"/><path d="M14 1v20M8 5h4M8 9h4M16 5h4M16 9h4"/></svg>Wardrobe</div>
    <div class="amenity"><svg viewBox="0 0 28 22" class="ico"><path d="M17 2v5M14 7h6M17 10v1M15 12v1M19 12v1M5 15h18v5H5z"/></svg>Ensuite shower</div>
    <div class="amenity"><svg viewBox="0 0 28 22" class="ico"><path d="M3 8h22v13H3zM3 12h22M14 8v13M6 3h16M9 3v5M14 3v5M19 3v5"/></svg>Kitchenette</div>
  </div>

  <h2 class="abs" style="left:444px;top:612px">Public Amenities</h2>
  <ul class="abs public" style="top:636px;width:120px">
    <li><svg viewBox="0 0 14 14" class="ico"><path d="M1 7h11l1-1M4 7l2-4h1.5L7 7M5 7l2 4h1.5L8 7M1.5 5.5L2.5 7"/></svg>Distance to the airport</li>
    <div class="sub">15 minutes by car</div>
    <li><svg viewBox="0 0 14 14" class="ico"><rect x="3" y="1.5" width="8" height="10" rx="1"/><path d="M3 7h8M4 13v-1.5M10 13v-1.5"/></svg>Busses<svg class="chev"><use href="#chev"/></svg></li>
    <li><svg viewBox="0 0 14 14" class="ico"><rect x="3" y="2" width="8" height="9" rx="1.5"/><path d="M3 7h8M4.5 13l1-2M9.5 13l-1-2"/></svg>Trains<svg class="chev"><use href="#chev"/></svg></li>
    <li><svg viewBox="0 0 14 14" class="ico"><path d="M2 10V7l1.5-3.5h7L12 7v3zM2 7h10M3 10v1.5M11 10v1.5"/></svg>Rent a car<svg class="chev"><use href="#chev"/></svg></li>
  </ul>
</section>

<section>
  <h2 class="abs" style="left:193px;top:749px">Location</h2>
  <div class="abs address" style="left:193px;top:771px">Larkspur Lane, WILLOWMERE HEIGHTS</div>
  <p class="abs description" style="left:193px;top:788px;width:240px">Donec lobortis urna sed urna tincidunt, a vulputate quam tempor. Donec et ultrices velit. Donec ac pretium justo, sit amet interdum nisi. Vestibulum elementum leo et viverra maximus. Donec molestie diam sagittis feugiat egestas. Proin sollicitudin quam arcu, mollis iaculis erat molestie nec. In finibus egestas facilisis.</p>
  <div class="abs map" style="left:444px;top:748px;width:242px;height:123px" role="img" aria-label="Street map of the surrounding neighbourhood with the room location marked"></div>
</section>

<section>
  <h2 class="abs" style="left:193px;top:916px">Similar Bedrooms</h2>
  <article class="card" style="left:193px">
    <div class="thumb t1" role="img" aria-label="Warmly lit bedroom with green bedding"></div>
    <div class="city">MELBOURNE</div>
    <div class="name">Luxury in the mountains</div>
    <div class="type">DOUBLE BEDROOM</div>
    <div class="rating"><svg><use href="#star"/></svg><svg><use href="#star"/></svg><svg><use href="#star"/></svg><svg><use href="#star"/></svg><svg><use href="#star-off"/></svg><span>&nbsp;180</span></div>
  </article>
  <article class="card" style="left:361px">
    <div class="thumb t2" role="img" aria-label="Bedroom with dark red walls and white bedding"></div>
    <div class="city">MELBOURNE</div>
    <div class="name">Cherry room</div>
    <div class="type">DOUBLE BEDROOM</div>
    <div class="rating"><svg><use href="#star"/></svg><svg><use href="#star"/></svg><svg><use href="#star"/></svg><svg><use href="#star"/></svg><svg><use href="#star-half"/></svg><span>&nbsp;215</span></div>
  </article>
  <article class="card" style="left:529px">
    <div class="thumb t3" role="img" aria-label="Bedroom with stone feature wall and blue bedding"></div>
    <div class="city">MELBOURNE</div>
    <div class="name">The wall</div>
    <div class="type">DOUBLE BEDROOM</div>
    <div class="rating"><svg><use href="#star"/></svg><svg><use href="#star"/></svg><svg><use href="#star"/></svg><svg><use href="#star"/></svg><svg><use href="#star"/></svg><span>&nbsp;432</span></div>
  </article>
</section>

<footer class="site-footer">
  <div class="abs rule"></div>
  <div class="abs footer-brand"><span class="brand-mark"></span>LodGivo</div>
  <ul class="abs footer-col" style="left:318px"><li>Paid methods</li><li>Cancellation policy</li><li>Other</li></ul>
  <ul class="abs footer-col" style="left:444px"><li>Conditions</li><li>Be a Landlor</li><li>Selling rooms</li></ul>
  <ul class="abs footer-col" style="left:570px"><li>Terms</li><li>Privacity</li><li>Sitemap</li></ul>
</footer>
</body>
</html>
```